Classic and neutral book cover design

We are looking for a classic and neutral book cover design to be used as the template for a series of books to be published. We are hence looking for a template that will allow us to easily change the title name for all books in this series.
The use of very few colours (black and white is welcome) and few design elements is a big bonus. As a source of inspiration we would like to ask you to view the very simple and
If you think you have a cool idea that can add a twist to the formal classic look don't hesitate. Go for it !
Work will be done for a 30 year old Sweden based cultural non-profit called VĂ©ru (www.verufoundation.example). We work with the publishing and supporting of post-modern art and literature addressing contemporary topics but are also involved in assisting projects of cultural preservation.
Target Market(s)
The audience is expected to have some form of interest in culture but could range from hobbyist readers to tenure track scholars
Industry/Entity Type
Non-Profit
Requirements
Must have
- General:
- Classic and neutral feel
- Preferably very simple and few shapes
- usage of few colours (black and white is welcome)
Information to be displayed on the cover is:
- Author
- Title
- type of work e.g. play/novel (optional)
- publishing house (in this case "Veru Publishing")
Nice to have
- ideas to prevent it from become boring are of course welcome
Should not have
- - too many colours

```html
<!DOCTYPE html>
<html lang="lv">
<head>
<meta charset="utf-8">
<title>Vērotājs – book cover</title>
<link rel="stylesheet" href="https://fonts.googleapis.com/css2?family=Alegreya:ital,wght@0,400;1,400&display=swap">
<style>
  :root {
    --page-bg: #efede8;
    --panel: #707070;
    --text-light: #ececec;
    --text-soft: #dcdcdc;
    --stripe-dark: #2a2a2a;
    --stripe-mid: #8a8a8a;
    --stripe-light: #cfcfcf;
  }
  html, body {
    margin: 0;
    width: 1200px;
    height: 1000px;
    overflow: hidden;
    background: var(--page-bg);
    font-family: "Alegreya", Georgia, serif;
  }
  .cover {
    position: absolute;
    left: 261px;
    top: 72px;
    width: 678px;
    height: 856px;
    box-shadow: 0 2px 5px rgba(0,0,0,0.25);
    overflow: hidden;
  }
  .cover-art {
    position: absolute;
    inset: 0;
    background: linear-gradient(100deg, var(--stripe-dark) 0%, var(--stripe-mid) 35%, var(--stripe-light) 50%, var(--stripe-mid) 65%, var(--stripe-dark) 100%);
  }
  .info-panel {
    position: absolute;
    left: 55px;
    top: 346px;
    right: 0;
    bottom: 0;
    background: var(--panel);
    color: var(--text-light);
  }
  .author, .title {
    position: absolute;
    left: 58px;
    margin: 0;
    font-size: 40px;
    font-weight: 400;
    line-height: 1;
    white-space: nowrap;
  }
  .author { top: 54px; }
  .separator {
    position: absolute;
    left: 58px;
    top: 124px;
    font-size: 34px;
    line-height: 1;
  }
  .title { top: 174px; }
  .genre {
    position: absolute;
    left: 58px;
    top: 222px;
    margin: 0;
    font-size: 21px;
    line-height: 1;
  }
  .publisher {
    position: absolute;
    left: 58px;
    top: 420px;
    margin: 0;
    font-size: 19px;
    line-height: 1;
    font-style: italic;
    color: var(--text-soft);
  }
</style>
</head>
<body>
  <div class="cover">
    <div class="cover-art" role="img" aria-label="Black, grey and white slanted vertical stripe pattern"></div>
    <div class="info-panel">
      <h2 class="author">Mikelis Dorenis</h2>
      <div class="separator">*</div>
      <h1 class="title">Vērotājs</h1>
      <p class="genre">drāma</p>
      <p class="publisher">Veru Publishing</p>
    </div>
  </div>
</body>
</html>
```